Stylish new business card needed!

Hello everyone! I am in need of a new business card design for an alarm company here in Hurricane WV. I have all fonts, color codes and logos provided for you use! We are a young company and like the style of a clean sleek looking business card. Would like it double sided, one side holding the logo and the other with your design!
Target Market(s)
The people that are looking for the newest tech for home automation and security
Industry/Entity Type
Alarm services; Home automation
Contact Information for Business Card
Name of person; position (Sales; Installer); Phone Number (555.418.7260); Employee cell Number; Website (www.GuardedByVelk.example); Employee Email; Double sided
Look and feel
Each slider illustrates characteristics of the customer's brand and the style your logo design should communicate.

```html
<!DOCTYPE html>
<html lang="en">
<head>
<meta charset="utf-8">
<title>Guarded By Velk — Business Card</title>
<link href="https://fonts.googleapis.com/css2?family=Arimo:wght@400;700&display=swap" rel="stylesheet">
<style>
  :root {
    --backdrop: #2b2b2e;
    --card-dark: #1f1f23;
    --brand-orange: #ee8443;
    --brand-grey: #8e8e92;
    --text-light: #f2f2f2;
    --rule: #77777c;
  }
  * { box-sizing: border-box; margin: 0; padding: 0; }
  html, body {
    width: 1200px; height: 780px; overflow: hidden;
    background: var(--backdrop);
    font-family: "Arimo", Arial, sans-serif;
  }
  .stage {
    position: relative; width: 1200px; height: 780px;
    display: flex; align-items: center; justify-content: center; gap: 50px;
  }
  .card {
    position: relative; width: 525px; height: 300px;
    border-radius: 4px;
    box-shadow: 0 14px 30px rgba(0,0,0,.45);
    overflow: hidden;
  }
  /* Front */
  .card--front { background: var(--card-dark); }
  .brand-block {
    position: absolute; left: 34px; top: 0; width: 215px; height: 100%;
    display: flex; align-items: center; justify-content: center;
  }
  .brand-name {
    color: var(--brand-orange);
    font-weight: 700; font-size: 27px; line-height: 1.15;
    letter-spacing: 1px; text-transform: uppercase; text-align: left;
  }
  .divider {
    position: absolute; left: 248px; top: 60px; width: 1px; height: 190px;
    background: var(--rule); transform: rotate(14deg);
  }
  .details {
    position: absolute; left: 282px; top: 96px; right: 20px;
  }
  .person-name { font-size: 27px; font-weight: 700; line-height: 1; white-space: nowrap; }
  .person-name .first { color: var(--brand-orange); }
  .person-name .last { color: var(--brand-grey); }
  .person-role {
    color: var(--text-light); font-size: 14px; font-weight: 700; margin: 6px 0 16px;
  }
  .contact-list { list-style: none; }
  .contact-item {
    display: flex; align-items: center; gap: 8px;
    color: var(--text-light); font-size: 14px; line-height: 21px; white-space: nowrap;
  }
  .contact-item svg { width: 12px; height: 12px; flex: none; }
  /* Back */
  .card--back { background: var(--brand-orange); }
  .back-field { position: absolute; inset: 0; background: linear-gradient(135deg, #f08a4a, #e47a3a); }
  .back-mark {
    position: absolute; right: 30px; bottom: 34px;
    color: #ffffff; font-weight: 700; font-size: 13px; letter-spacing: .5px;
    text-transform: uppercase;
  }
</style>
</head>
<body>
<main class="stage">
  <section class="card card--front" aria-label="Card front">
    <div class="brand-block">
      <p class="brand-name">Guarded By<br>Velk</p>
    </div>
    <div class="divider"></div>
    <div class="details">
      <h1 class="person-name"><span class="first">Marta</span> <span class="last">Dolinska</span></h1>
      <p class="person-role">Sales; Installer</p>
      <ul class="contact-list">
        <li class="contact-item">
          <svg viewBox="0 0 12 12" aria-hidden="true"><path d="M2.5 1l2 2.2-1 1.3c.7 1.5 1.8 2.6 3.3 3.3l1.3-1 2.2 2-1.2 1.7C5.5 10.3 1.7 6.5 1 2.2z" fill="var(--brand-orange)"/></svg>
          555.418.7260
        </li>
        <li class="contact-item">
          <svg viewBox="0 0 12 12" aria-hidden="true"><rect x="3" y="1" width="6" height="10" rx="1" fill="none" stroke="var(--text-light)" stroke-width="1"/></svg>
          555.902.3318
        </li>
        <li class="contact-item">
          <svg viewBox="0 0 12 12" aria-hidden="true"><circle cx="6" cy="6" r="5" fill="var(--brand-orange)"/><path d="M1 6h10M6 1c-2 3-2 7 0 10M6 1c2 3 2 7 0 10" stroke="var(--card-dark)" stroke-width=".8" fill="none"/></svg>
          www.GuardedByVelk.example
        </li>
        <li class="contact-item">
          <svg viewBox="0 0 12 12" aria-hidden="true"><rect x="1" y="3" width="10" height="7" fill="var(--brand-orange)"/><path d="M1 3l5 4 5-4" stroke="var(--card-dark)" stroke-width=".8" fill="none"/></svg>
          info@GuardedByVelk.example
        </li>
      </ul>
    </div>
  </section>

  <section class="card card--back" aria-label="Card back">
    <div class="back-field" role="img" aria-label="Repeating brand-name pattern in darker orange tones across the card"></div>
    <p class="back-mark">Guarded By Velk</p>
  </section>
</main>
</body>
</html>
```